Heron Haulage needs Bussiness cards!

Our new trucking company needs business cards!
We need the same design with two different names and emails, everything else it's the same.
I have included our original logo so we can use it for the design.
Note: the logo to be used is the o e with the buffalo on the right side, next to the letters H and H.

Target Market(s)

Trucking, refrigerated transportation, freight

Industry/Entity Type

Business

Contact Information for Business Card

Card #1:
Marcus Whitfield
marcuswhitfield@heronhaulage.example
1-855-317-6094
(956)238-7160
4117 W. Larkin Ave.
Pharr, TX 78590
www.heronhaulage.example

Card#2:
Rosalba Quintero
rosalba@heronhaulage.example
1-855-317-6094
(956)238-7160
4117 W. Larkin Ave.
Pharr, TX 78590
www.heronhaulage.example

Font styles to use
Sans Serif

Colors
0655a3
ec1f27
ffffff

Requirements
Must have
• our logo
Nice to have
• roads on background,

```html
<!DOCTYPE html>
<html lang="en">
<head>
<meta charset="utf-8">
<title>Heron Haulage — Business Cards</title>
<link rel="stylesheet" href="https://fonts.googleapis.com/css2?family=Open+Sans:wght@400;600;700;800&display=swap">
<style>
  :root {
    --backdrop: #e9e9ea;
    --card-white: #f7f7f7;
    --navy: #0b3560;
    --red: #c8202b;
    --ink: #3a3a3a;
    --white: #ffffff;
  }
  * { margin: 0; padding: 0; box-sizing: border-box; }
  html, body {
    width: 1200px; height: 900px; overflow: hidden;
    background: var(--backdrop);
    font-family: "Open Sans", Arial, sans-serif;
  }
  .canvas { position: relative; width: 1200px; height: 900px; }
  .card {
    position: absolute; width: 525px; height: 300px;
    box-shadow: 0 6px 18px rgba(0,0,0,0.12);
  }
  .card--front { left: 45px; background: var(--card-white); }
  .card--first { top: 120px; }
  .card--second { top: 480px; }
  .card--back {
    left: 630px; top: 300px; background: var(--navy);
    display: flex; align-items: center; justify-content: center;
  }
  .brand {
    position: absolute; left: 40px; top: 38px;
    display: flex; align-items: center; gap: 10px;
  }
  .brand__mark { width: 14px; height: 14px; border-radius: 50%; background: var(--red); }
  .brand__name {
    font-weight: 800; font-size: 26px; color: var(--navy);
    text-transform: uppercase; letter-spacing: 0.5px;
  }
  .contact {
    position: absolute; left: 40px; top: 98px;
    list-style: none; font-size: 12.5px; color: var(--ink); line-height: 19px;
  }
  .contact li { display: flex; align-items: center; gap: 8px; white-space: nowrap; }
  .contact svg { width: 11px; height: 11px; fill: var(--navy); flex: none; }
  .holder {
    position: absolute; right: 40px; bottom: 60px;
    font-size: 16px; font-weight: 600; white-space: nowrap;
  }
  .holder__first { color: var(--red); }
  .holder__last { color: var(--navy); }
  .back-brand {
    font-weight: 800; font-size: 46px; color: var(--white);
    text-transform: uppercase; letter-spacing: 1px; white-space: nowrap;
  }
</style>
</head>
<body>
<main class="canvas">
  <section class="card card--front card--first" aria-label="Business card front, Marcus Whitfield">
    <div class="brand">
      <span class="brand__mark"></span>
      <span class="brand__name">Heron Haulage</span>
    </div>
    <ul class="contact">
      <li><svg viewBox="0 0 12 12"><rect x="3" y="0.5" width="6" height="11" rx="1.2"/></svg>(956)238-7160</li>
      <li><svg viewBox="0 0 12 12"><path d="M2 1h3l1 3-1.5 1a7 7 0 0 0 2.5 2.5L8 6l3 1v3a1 1 0 0 1-1 1A9 9 0 0 1 1 2a1 1 0 0 1 1-1z"/></svg>1-855-317-6094</li>
      <li><svg viewBox="0 0 12 12"><path d="M0.5 2.5h11v7h-11z M0.5 2.5 6 7l5.5-4.5" stroke="#f7f7f7" stroke-width="0.8"/></svg>marcuswhitfield@heronhaulage.example</li>
      <li><svg viewBox="0 0 12 12"><circle cx="6" cy="6" r="5.5"/></svg>www.heronhaulage.example</li>
      <li>4117 W. Larkin Ave.</li>
      <li>Pharr, TX 78590</li>
    </ul>
    <p class="holder"><span class="holder__first">Marcus</span> <span class="holder__last">Whitfield</span></p>
  </section>

  <section class="card card--front card--second" aria-label="Business card front, Rosalba Quintero">
    <div class="brand">
      <span class="brand__mark"></span>
      <span class="brand__name">Heron Haulage</span>
    </div>
    <ul class="contact">
      <li><svg viewBox="0 0 12 12"><rect x="3" y="0.5" width="6" height="11" rx="1.2"/></svg>(956)238-7160</li>
      <li><svg viewBox="0 0 12 12"><path d="M2 1h3l1 3-1.5 1a7 7 0 0 0 2.5 2.5L8 6l3 1v3a1 1 0 0 1-1 1A9 9 0 0 1 1 2a1 1 0 0 1 1-1z"/></svg>1-855-317-6094</li>
      <li><svg viewBox="0 0 12 12"><path d="M0.5 2.5h11v7h-11z M0.5 2.5 6 7l5.5-4.5" stroke="#f7f7f7" stroke-width="0.8"/></svg>rosalba@heronhaulage.example</li>
      <li><svg viewBox="0 0 12 12"><circle cx="6" cy="6" r="5.5"/></svg>www.heronhaulage.example</li>
      <li>4117 W. Larkin Ave.</li>
      <li>Pharr, TX 78590</li>
    </ul>
    <p class="holder"><span class="holder__first">Rosalba</span> <span class="holder__last">Quintero</span></p>
  </section>

  <section class="card card--back" aria-label="Business card back">
    <span class="back-brand">Heron Haulage</span>
  </section>
</main>
</body>
</html>
```